real esate business card with company logo and name

we need a business card design for a real esate company

The company name is Walsh & Brand Pty Ltd, and we have our logo designed and will upload. We want classic or moden feel. Black or white background. looks more textured. Should include folowinginformations
Owen Walsh and Lucy Brand
Sales Agents & Onsite Manager
p: 07 5948 2063
F: 07 5948 2174
M:0431 857 219
3/42 Marlow Crescent, FERNLEA QLD 4213

We want this business card looks professonal. Thank you in advance.

Industry/Entity Type

Real Estate Agent

Contact Information for Business Card

Owen Walsh and Lucy Brand
Onsite Manager & Sales Agents
p: 07 5948 2063
M:0431 857 219

Font styles to use
Serif

Colors
000000
fbfbfb
333333
959595

Requirements
Must have
• company logo and name, black or white back ground

```html
<!DOCTYPE html>
<html lang="en">
<head>
<meta charset="utf-8">
<title>Walsh &amp; Brand Pty Ltd — Business Card</title>
<link rel="stylesheet" href="https://fonts.googleapis.com/css2?family=Roboto+Condensed:wght@400;500&family=Open+Sans:wght@400&display=swap">
<style>
  :root {
    --backdrop: #a9a6a7;
    --card: #fbfbfb;
    --ink-dark: #333333;
    --ink-mid: #555558;
    --ink-soft: #8c8b90;
    --icon: #b3b3b3;
    --mark: #5a5a5d;
    --band-dark: #4a4a4d;
    --band-light: #c4c4c6;
  }
  * { box-sizing: border-box; margin: 0; padding: 0; }
  html, body { width: 1200px; height: 1200px; overflow: hidden; }
  body {
    position: relative;
    background: var(--backdrop);
    font-family: "Open Sans", sans-serif;
  }
  .card {
    position: absolute;
    width: 712px;
    height: 412px;
    background: var(--card);
    border-radius: 24px;
    overflow: hidden;
  }
  .card--front { left: 238px; top: 118px; }
  .card--back  { left: 234px; top: 645px; }

  .brand-square {
    position: absolute;
    width: 112px;
    height: 112px;
    background: var(--mark);
  }
  .company-name {
    position: absolute;
    font-family: "Roboto Condensed", sans-serif;
    font-weight: 400;
    font-size: 25px;
    letter-spacing: 0.3px;
    color: var(--ink-soft);
    white-space: nowrap;
    text-transform: uppercase;
  }
  .card--front .brand-square { left: 300px; top: 122px; }
  .card--front .company-name { left: 0; width: 712px; text-align: center; top: 289px; }

  .card--back .brand-square { left: 109px; top: 117px; }
  .card--back .company-name { left: 0; width: 330px; text-align: center; top: 278px; }

  .contact { position: absolute; left: 378px; top: 86px; }
  .contact__names {
    font-family: "Roboto Condensed", sans-serif;
    font-weight: 400;
    font-size: 26px;
    color: var(--ink-dark);
    white-space: nowrap;
  }
  .contact__role {
    font-family: "Roboto Condensed", sans-serif;
    font-size: 15px;
    color: var(--ink-dark);
    margin-top: 7px;
  }
  .contact__lines { list-style: none; margin-top: 42px; }
  .contact__lines li {
    display: flex;
    align-items: center;
    height: 26px;
    font-size: 16px;
    color: var(--ink-mid);
    letter-spacing: 0.3px;
  }
  .contact__lines svg { width: 16px; height: 16px; margin-right: 19px; fill: var(--icon); }
  .contact__address {
    margin-top: 8px;
    font-size: 16px;
    line-height: 28px;
    color: var(--ink-mid);
  }
  .card__band { position: absolute; left: 0; bottom: 0; width: 712px; height: 20px; }
</style>
</head>
<body>

  <section class="card card--front" aria-label="Card front">
    <div class="brand-square" aria-hidden="true"></div>
    <p class="company-name">Walsh &amp; Brand Pty Ltd.</p>
  </section>

  <section class="card card--back" aria-label="Card back">
    <div class="brand-square" aria-hidden="true"></div>
    <p class="company-name">Walsh &amp; Brand Pty Ltd.</p>

    <div class="contact">
      <h1 class="contact__names">Owen Walsh &amp; Lucy Brand</h1>
      <p class="contact__role">Sales Agents &amp; Onsite Manager</p>
      <ul class="contact__lines">
        <li>
          <svg viewBox="0 0 16 16" aria-label="Mobile"><path d="M4 0h8a1 1 0 0 1 1 1v14a1 1 0 0 1-1 1H4a1 1 0 0 1-1-1V1a1 1 0 0 1 1-1zm1 2v10h6V2zm3 11a1 1 0 1 0 0 2 1 1 0 0 0 0-2z"/></svg>
          0431 857 219
        </li>
        <li>
          <svg viewBox="0 0 16 16" aria-label="Phone"><path d="M1 5c0-2 3-3 7-3s7 1 7 3v1h-4V4.5H5V6H1zM4 7h8l3 4v3H1v-3zm4 1.5a2 2 0 1 0 0 4 2 2 0 0 0 0-4z"/></svg>
          07 5948 2063
        </li>
        <li>
          <svg viewBox="0 0 16 16" aria-label="Fax"><path d="M4 0h8v5H4zM1 6h14v7H12v3H4v-3H1zm4 5v4h6v-4z"/></svg>
          07 5948 2174
        </li>
      </ul>
      <address class="contact__address" style="font-style:normal">
        3/42 Marlow Crescent,<br>FERNLEA QLD 4213
      </address>
    </div>

    <svg class="card__band" viewBox="0 0 712 20" preserveAspectRatio="none" aria-hidden="true">
      <rect x="0" y="0" width="712" height="20" fill="var(--band-light)"/>
      <polygon points="0,2 500,2 478,20 0,20" fill="var(--band-dark)"/>
    </svg>
  </section>

</body>
</html>
```